Luxury travel agency needs a website design

We are a travel agency specializing in booking luxury vacations. We specialize in Hawaii, Europe and Caribbean, but will do all vacations. I want a very classy website design which would attract luxury clients. The company name is "Harbors and Hammocks Travel Agency". Would love the web design to go with the color scheme of the logo. Hex codes included in files. Logo is attached. Would also love more Grey in the website. I want it very elegant

Coding

Coded - Design and coding required

Font styles to use
Sans Serif
Decorative

Requirements
Must have
• - Consultation Tab or a page where the client can fill out a short form about what vacation that they would want to book. I want this info to be sent to me in order for me to contact them.
- Somewhere with my contact info "email: marla@harborsandhammockstravel.example and phone number"
- Social media links
- About section "Marla Dunbevy - Agency Owner (picture provided)
Marla has been traveling full time for the passed two years and has been very passionate about travel from a young age. Marla is dedicated to working closely with clients to book their dream vacation.
Marla's specializations include honeymoons and anniversaries focusing on travel in Europe, Hawaii and all inclusive resorts in the Caribbean.

```html
<!DOCTYPE html>
<html lang="en">
<head>
<meta charset="utf-8">
<title>Harbors &amp; Hammocks Travel Agency</title>
<link rel="stylesheet" href="https://fonts.googleapis.com/css2?family=Almendra+SC&family=Work+Sans:wght@400;500;600&display=swap">
<style>
:root{
  --stage:#3a3533;
  --page:#ffffff;
  --wood:#c9a77c;
  --sand:#ebe3d0;
  --sand-light:#f4efe3;
  --grey:#5b5a5e;
  --ink:#3b3a3c;
  --text:#6a6866;
  --orange:#f39a3e;
  --orange-light:#f7c35a;
  --line:#e2ddd3;
}
*{box-sizing:border-box;margin:0;padding:0}
html,body{width:1200px;height:3883px;overflow:hidden;background:var(--stage)}
body{font-family:"Work Sans",sans-serif;color:var(--text)}
.page{position:absolute;left:72px;top:60px;width:1055px;height:3764px;background:var(--page);overflow:hidden}
.abs{position:absolute}
.deco{font-family:"Almendra SC",serif;color:var(--ink);font-weight:400}
.photo{position:absolute}

/* header */
.header{left:0;top:0;width:1055px;height:84px;background:linear-gradient(90deg,#c69f72,#d8b88e 40%,#caa477 70%,#d3b184)}
.nav a{position:absolute;top:34px;font-family:"Almendra SC",serif;font-size:15px;color:#4a3b2c;text-decoration:none}
.brand-plate{left:425px;top:0;width:205px;height:108px;background:#fff;border-radius:0 0 100px 100px/0 0 30px 30px;display:flex;flex-direction:column;align-items:center;justify-content:center;gap:4px}
.brand-dot{width:22px;height:22px;border-radius:50%;background:var(--orange)}
.brand-name{font-family:"Almendra SC",serif;font-size:16px;color:var(--ink);text-align:center;line-height:1.1}
.brand-sub{font-size:7px;letter-spacing:2px;color:var(--ink)}

/* hero */
.hero{left:0;top:84px;width:1055px;height:478px;background:linear-gradient(180deg,#8fa8c2 0%,#c7d2de 38%,#4c8fb1 58%,#2f6f93 100%)}
.hero-title{left:0;top:230px;width:1055px;text-align:center;font-family:"Almendra SC",serif;font-size:62px;color:#fff;text-shadow:0 2px 6px rgba(0,0,0,.35)}
.arrow{width:48px;height:48px;border:1.5px solid rgba(255,255,255,.8);border-radius:50%;display:flex;align-items:center;justify-content:center}

/* booking bar */
.booking{left:112px;top:513px;width:831px;height:109px;background:#fff;box-shadow:0 6px 18px rgba(0,0,0,.12);display:flex}
.field{flex:1;padding:20px 0 0 24px;border-right:1px solid var(--line);margin:20px 0;padding-top:0}
.field:last-of-type{border-right:none}
.field .lbl{font-size:13px;color:var(--text);display:flex;gap:6px;align-items:center}
.field .lbl i{width:9px;height:12px;background:var(--orange-light);border-radius:50% 50% 2px 2px;display:inline-block}
.field .val{font-family:"Almendra SC",serif;font-size:26px;color:var(--ink);margin-top:6px;display:flex;align-items:baseline;gap:4px}
.field .val small{font-size:11px}
.field .val b{margin-left:auto;margin-right:18px;font-size:12px;font-weight:400}
.consult{width:174px;background:linear-gradient(90deg,var(--orange-light),var(--orange));display:flex;align-items:center;justify-content:center}
.consult span{border:1px solid #fff;color:#fff;font-family:"Almendra SC",serif;font-size:17px;padding:8px 10px}

/* about */
.about-bg{left:0;top:562px;width:1055px;height:432px;background:linear-gradient(180deg,var(--sand) 70%,#fff)}
.h2{font-family:"Almendra SC",serif;font-size:34px;color:var(--ink)}
.about-text{left:98px;top:764px;width:420px;font-size:14px;line-height:24px;color:var(--text)}
.about-text p+p{margin-top:16px}
.frame{background:#fff;padding:8px;box-shadow:0 4px 14px rgba(0,0,0,.15)}

/* tours */
.kicker{font-size:13px;color:var(--text)}
.tour{background:#fff;padding:8px;box-shadow:0 3px 12px rgba(0,0,0,.18)}
.tour .img{width:100%;height:100%;position:relative}
.tour .cap{position:absolute;left:12px;bottom:26px;color:#fff}
.tour .cap small{font-size:13px;display:block;margin-bottom:4px}
.tour .cap strong{font-family:"Almendra SC",serif;font-size:20px;font-weight:400}
.book-btn{display:inline-block;margin-top:12px;border:1px solid #fff;padding:6px 24px;font-size:12px;font-weight:600;letter-spacing:1px}

/* escape */
.escape-bg{left:0;top:1703px;width:1055px;height:626px;background:linear-gradient(180deg,#fff 0%,var(--sand) 10%,var(--sand) 88%,#fff 100%)}
.center{text-align:center;left:0;width:1055px}
.lead{font-size:13px;line-height:22px;color:var(--text)}
.feature{width:300px;text-align:center}
.ring{width:108px;height:108px;margin:0 auto;border-radius:50%;background:#fff;display:flex;align-items:center;justify-content:center;box-shadow:0 2px 8px rgba(0,0,0,.1)}
.ring span{width:92px;height:92px;border-radius:50%;background:var(--grey);display:flex;align-items:center;justify-content:center}
.feature h3{font-family:"Almendra SC",serif;font-size:19px;font-weight:400;color:var(--ink);margin-top:28px}
.feature p{font-size:11.5px;line-height:19.5px;margin-top:12px;color:var(--text)}

/* rooms */
.room{top:2409px;height:302px;border:5px solid #fff;box-shadow:0 2px 8px rgba(0,0,0,.2)}
.room-card{left:172px;top:2434px;width:231px;height:249px;background:#fff;padding:18px 16px}
.room-card h3{font-family:"Almendra SC",serif;font-size:28px;font-weight:400;color:var(--ink);margin-top:8px}
.room-card p{font-size:11.5px;line-height:19.5px;margin-top:6px}
.dots{display:flex;gap:6px;margin-top:14px}
.dots i{width:20px;height:2px;background:var(--grey)}
.dots i:first-child{background:var(--orange)}

/* contact */
.contact-bg{left:0;top:2759px;width:1055px;height:678px;background:linear-gradient(180deg,#fff,#f3f1ee 40%,#f1efec 85%,#fff)}
.input{background:#fff;border:1px solid var(--line);font-size:12px;letter-spacing:1px;color:#9a9590;display:flex;align-items:center;gap:10px;padding-left:12px}
.input i{width:11px;height:11px;background:var(--orange-light);border-radius:2px}
.textarea{align-items:flex-start;padding-top:18px}
.submit{left:443px;top:3321px;width:170px;height:36px;background:linear-gradient(90deg,var(--orange-light),var(--orange));color:#fff;font-size:12px;font-weight:600;display:flex;align-items:center;justify-content:center;letter-spacing:1px}

/* footer */
.foot-brand{left:109px;top:3475px;width:233px;text-align:center}
.foot-brand .brand-dot{margin:0 auto 8px;width:34px;height:34px}
.foot-brand .brand-name{font-size:24px}
.social{top:3628px;width:40px;height:40px;border:1.5px solid var(--orange);border-radius:50%}
.col h4{font-family:"Almendra SC",serif;font-size:17px;font-weight:400;color:var(--ink);border-bottom:2px solid var(--orange);display:inline-block;padding-bottom:2px;margin-bottom:22px}
.col li{list-style:none;font-size:12px;line-height:22.6px;color:var(--ink)}
.info{font-size:12px;line-height:22px;color:var(--ink);display:flex;gap:12px}
.info svg{flex:none;margin-top:5px}
.rule{left:101px;top:3689px;width:859px;height:1px;background:var(--orange-light)}
.fine{font-size:12px;color:var(--ink)}
.totop{left:993px;top:3685px;width:28px;height:28px;border-radius:50%;background:var(--orange);display:flex;align-items:center;justify-content:center}
</style>
</head>
<body>
<div class="page">

  <header class="abs header" role="img" aria-label="Wood plank texture"></header>
  <nav class="nav">
    <a style="left:128px">Home</a>
    <a style="left:203px">About Us</a>
    <a style="left:312px">Services</a>
    <a style="left:681px">News</a>
    <a style="left:757px">Reviews</a>
    <a style="left:853px">Contact Us</a>
  </nav>
  <div class="abs brand-plate">
    <div class="brand-dot"></div>
    <div class="brand-name">Harbors &amp; Hammocks</div>
    <div class="brand-sub">TRAVEL AGENCY</div>
  </div>

  <section class="abs hero" role="img" aria-label="Wooden stilt house standing in a turquoise sea under a cloudy sky"></section>
  <h1 class="abs hero-title">Harbors &amp; Hammocks</h1>
  <div class="abs arrow" style="left:24px;top:256px"><svg width="18" height="12" viewBox="0 0 18 12"><path d="M17 6H2M6 1L1 6l5 5" fill="none" stroke="#fff" stroke-width="1.5"/></svg></div>
  <div class="abs arrow" style="left:980px;top:256px"><svg width="18" height="12" viewBox="0 0 18 12"><path d="M1 6h15M12 1l5 5-5 5" fill="none" stroke="#fff" stroke-width="1.5"/></svg></div>

  <div class="abs about-bg"></div>

  <form class="abs booking">
    <div class="field"><div class="lbl"><i></i>Arrival</div><div class="val">05 <small>May</small><b>⌄</b></div></div>
    <div class="field"><div class="lbl"><i></i>Departure</div><div class="val">15 <small>May</small><b>⌄</b></div></div>
    <div class="field"><div class="lbl"><i></i>Adults</div><div class="val">02<b>⌄</b></div></div>
    <div class="field"><div class="lbl"><i></i>Children</div><div class="val">01<b>⌄</b></div></div>
    <div class="field"><div class="lbl"><i></i>Rooms</div><div class="val">01<b>⌄</b></div></div>
    <div class="consult"><span>Consultation</span></div>
  </form>

  <h2 class="abs h2" style="left:98px;top:682px">About Marla Dunbevy</h2>
  <div class="abs about-text">
    <p>Marla has been traveling full time for the passed two years and has been very passionate about travel from a young age. Marla is dedicated to working closely with clients to book their dream vacation.</p>
    <p>Marla's specializations include honeymoons and anniversaries focusing on travel in Europe, Hawaii and all inclusive resorts in the Caribbean.</p>
  </div>
  <div class="abs frame" style="left:577px;top:648px;width:333px;height:335px">
    <div style="width:100%;height:100%;background:linear-gradient(160deg,#7d6a55,#a88b6e 50%,#4aa3c0)" role="img" aria-label="Portrait of agency owner Marla Dunbevy"></div>
  </div>

  <div class="abs kicker" style="left:98px;top:1078px">Will do all vacations</div>
  <h2 class="abs h2" style="left:98px;top:1100px">Our Popular Tours</h2>

  <div class="abs tour" style="left:98px;top:1173px;width:270px;height:211px">
    <div class="img" style="background:linear-gradient(180deg,#8fb8c9,#6e8b5c 60%,#2b2b2b)" role="img" aria-label="Palm trees over a Hawaiian beach"><div class="cap"><small>Special Packs Available</small><strong>Hawaii</strong></div></div>
  </div>
  <div class="abs tour" style="left:392px;top:1173px;width:270px;height:211px">
    <div class="img" style="background:linear-gradient(180deg,#4a8fd0,#9fc3e6 50%,#3b3b30)" role="img" aria-label="Eiffel Tower under a blue sky"><div class="cap"><small>Normal Packs Available</small><strong>Europe</strong></div></div>
  </div>
  <div class="abs tour" style="left:685px;top:1173px;width:271px;height:452px">
    <div class="img" style="background:linear-gradient(180deg,#6fa6d6,#c25a4a 50%,#3e7d4a 75%,#222)" role="img" aria-label="Colorful Caribbean beach huts beneath a palm tree"><div class="cap"><small>Special Packs Available</small><strong>Caribbean</strong></div></div>
  </div>
  <div class="abs tour" style="left:98px;top:1415px;width:564px;height:210px">
    <div class="img" style="background:linear-gradient(90deg,#1f5c9c,#5d86b2 40%,#8a7e6c 60%,#2d5f99)" role="img" aria-label="Tower Bridge in London under a blue sky"><div class="cap"><small>All Packs Available</small><strong>All Vacations</strong><br><span class="book-btn">BOOK NOW</span></div></div>
  </div>

  <div class="abs escape-bg"></div>
  <div class="abs center kicker" style="top:1810px">CALL TO ACTION</div>
  <h2 class="abs center h2" style="top:1830px">The Thin Escape</h2>
  <p class="abs center lead" style="top:1880px;left:210px;width:635px">Sed ut perspiciatis unde omnis iste natus error sit voluptatem accusantium doloremque laudantium totam remaperiam eaque ipsaquaealo</p>

  <div class="abs feature" style="left:70px;top:1964px">
    <div class="ring"><span><svg width="44" height="44" viewBox="0 0 44 44" fill="none" stroke="#f7c35a" stroke-width="2"><path d="M8 36l28-28M20 10l14 4-6 6M10 20l4 14 6-6M12 32l-4 4"/></svg></span></div>
    <h3>Easy &amp; Free Transport</h3>
    <p>Lorem ipsum dolor sit ametconsectetur adipiscing elitseddo eiusmod tempor incididunt utlaboreet dolore magna aliqua. Utenim adminim veniam</p>
  </div>
  <div class="abs feature" style="left:377px;top:1964px">
    <div class="ring"><span><svg width="44" height="44" viewBox="0 0 44 44" fill="none" stroke="#f7c35a" stroke-width="2"><rect x="8" y="22" width="16" height="14"/><path d="M28 36h10M26 20h12l-2 16h-8zM32 20l3-10"/></svg></span></div>
    <h3>Clean &amp; Fresh Food</h3>
    <p>Lorem ipsum dolor sit ametconsectetur adipiscing elitseddo eiusmod tempor incididunt utlaboreet dolore magna aliqua. Utenim adminim veniam</p>
  </div>
  <div class="abs feature" style="left:685px;top:1964px">
    <div class="ring"><span><svg width="44" height="44" viewBox="0 0 44 44" fill="none" stroke="#f7c35a" stroke-width="2"><path d="M16 30V10a4 4 0 0 1 8 0M28 30V10a4 4 0 0 1 8 0M16 16h12M16 24h12M6 34q4-3 8 0t8 0 8 0 8 0"/></svg></span></div>
    <h3>Play Ground &amp; Swiming Pool</h3>
    <p>Lorem ipsum dolor sit ametconsectetur adipiscing elitseddo eiusmod tempor incididunt utlaboreet dolore magna aliqua. Utenim adminim veniam</p>
  </div>

  <div class="abs room" style="left:3px;width:276px;background:linear-gradient(135deg,#e9e7e3,#b9b3aa)" role="img" aria-label="Bright living room with grey sofa"></div>
  <div class="abs room" style="left:300px;width:276px;background:linear-gradient(135deg,#4a3e35,#cbbfae 55%,#6b5443)" role="img" aria-label="Warm hotel bedroom"></div>
  <div class="abs room" style="left:597px;width:276px;background:linear-gradient(135deg,#dcdad6,#a9a6a0 60%,#5b5752)" role="img" aria-label="Modern grey bedroom with large windows"></div>
  <div class="abs room" style="left:894px;width:170px;background:linear-gradient(135deg,#e3e1dc,#8c8a88)" role="img" aria-label="Open plan lounge"></div>
  <div class="abs room-card">
    <svg width="40" height="34" viewBox="0 0 40 34" fill="none" stroke="#f7c35a" stroke-width="1.6"><path d="M4 30h32M8 30V14h24v16M12 14V8h16v6M20 2v6"/></svg>
    <h3>Luxury Room</h3>
    <p>Lorem ipsum dolor sit ametcon sectetur adipisicing elitseddo eiusmod tempor incididunt utlaboreet dolore magna aliqua. Utenim adminim veniam</p>
    <div class="dots"><i></i><i></i><i></i><i></i><i></i></div>
  </div>

  <div class="abs contact-bg"></div>
  <div class="abs center kicker" style="top:2910px">Get in touch</div>
  <h2 class="abs center h2" style="top:2930px">Contact Us</h2>
  <p class="abs center lead" style="top:2980px;left:210px;width:635px">Sed ut perspiciatis unde omnis iste natus error sit voluptatem accusantium doloremque laudantium totam remaperiam eaque ipsaquaealo</p>
  <div class="abs input" style="left:247px;top:3045px;width:272px;height:45px"><i></i>FIRST NAME</div>
  <div class="abs input" style="left:534px;top:3045px;width:276px;height:45px"><i></i>LAST NAME</div>
  <div class="abs input" style="left:247px;top:3111px;width:272px;height:45px"><i></i>EMAIL</div>
  <div class="abs input" style="left:534px;top:3111px;width:276px;height:45px"><i></i>PHONE</div>
  <div class="abs input textarea" style="left:247px;top:3178px;width:563px;height:120px"><i></i>MESSAGE</div>
  <div class="abs submit">SUBMIT</div>

  <div class="abs foot-brand">
    <div class="brand-dot"></div>
    <div class="brand-name">Harbors &amp; Hammocks</div>
    <div class="brand-sub">TRAVEL AGENCY</div>
  </div>
  <a class="abs social" style="left:123px" aria-label="Social link"></a>
  <a class="abs social" style="left:176px" aria-label="Social link"></a>
  <a class="abs social" style="left:230px" aria-label="Social link"></a>
  <a class="abs social" style="left:284px" aria-label="Social link"></a>

  <div class="abs col" style="left:401px;top:3494px"><h4>Quick Links</h4>
    <ul><li>Home</li><li>About Us</li><li>Services</li><li>News</li><li>Reviews</li><li>Contact Us</li></ul></div>
  <div class="abs col" style="left:556px;top:3494px"><h4>Links</h4>
    <ul><li>Copyright</li><li>Legal</li><li>Privacy</li><li>Accessibility</li><li>Sitemap</li></ul></div>
  <div class="abs col" style="left:715px;top:3494px;width:280px"><h4>Contact Info</h4>
    <div class="info"><svg width="12" height="14" viewBox="0 0 12 14"><path d="M6 13S1 8 1 5a5 5 0 0 1 10 0c0 3-5 8-5 8z" fill="#555"/><circle cx="6" cy="5" r="1.8" fill="#fff"/></svg><span>118 Palmetto Lane, Covington, Louisiana</span></div>
    <div class="info" style="margin-top:14px"><svg width="13" height="10" viewBox="0 0 13 10"><rect x=".5" y=".5" width="12" height="9" fill="none" stroke="#555"/><path d="M.5.5l6 5 6-5" fill="none" stroke="#555"/></svg><span>marla@harborsandhammockstravel.example</span></div>
    <div class="info" style="margin-top:20px"><svg width="12" height="12" viewBox="0 0 12 12"><path d="M2 1l2.5 2.5-1.5 1.5a7 7 0 0 0 4 4l1.5-1.5L11 10l-1.5 1.5C5 11 1 7 .5 2.5z" fill="#555"/></svg><span>555 014 2290</span></div>
  </div>

  <div class="abs rule"></div>
  <div class="abs fine" style="left:104px;top:3712px">Copyright © 2021 | All rights reserved</div>
  <div class="abs fine" style="left:733px;top:3712px">Privacy Policy</div>
  <div class="abs" style="left:841px;top:3700px;width:1px;height:30px;background:var(--orange-light)"></div>
  <div class="abs fine" style="left:867px;top:3712px">Terms and Use</div>
  <div class="abs totop"><svg width="10" height="6" viewBox="0 0 10 6"><path d="M1 5l4-4 4 4" fill="none" stroke="#fff" stroke-width="1.5"/></svg></div>

</div>
</body>
</html>
```